Law Firm Web Design Project

I need a website design for my law firm. I have attached to this description the URL of a website I liked with a description of the elements of that website that appeal to me.

I am also attaching my law firm's logo, so you can review that design when you create the website design.

Reference Site: www.harborfieldcounsel-example.com

What we like about this site:
• The different layers
• Subtle designs, textures, curves
• 3 dimensional
• Floating effect
• Simple logo that stands out (we are providing logo)
• Prominent phone number
• Location of Areas of Practice
oDivorce, Legal Separation, Paternity, Spousal Maintenance, Child Custody, Child Support, Protective Orders, Community Property, Business Evaluations
• The limited amount of links across the top
o Home, Meet Our Attorney, FAQ, Contact Us
• Request A Consultation click through
• Right side bar with the moving icons
• Badges

Other Tips:
• We don’t want the website to be dark. The logo can standout and the website can have its own colors and flow.
• We would like there to be a “call to action” or way to get in touch on every page and every page view
• We would like a place for credit card icons at the bottom of the page
• Strong, yet elegant
• Finally, just use the website provided as a guide. Explore different colors, textures, shapes, shadows etc.
Updates

I would prefer the website have colors that are complementary to my logo and that are strong and elegant.  I like black, gold, amber, and tan colors.  Black should be used sparingly as an accent only, since I don't want the website to be too dark.

Please review the website I provided as an example in my project description.  I really like the three dimensional aspects of that website (web page floating on top of a background and the logo in the upper left floating on top of the web page).  I also like the use of "swirling" on the background and the webpage.  I hope this additional information is helpful.

Requirements
Must have
• I need a place to insert "client testimonials", a place to insert four logos of awards the law firm has received, a place for people to fill out a form to contact the law firm via email, and a place for people to click to review articles I have written.

```html
<!DOCTYPE html>
<html lang="en">
<head>
<meta charset="utf-8">
<title>Ashcombe Law</title>
<link href="https://fonts.googleapis.com/css2?family=Open+Sans:wght@300;400;600;700&family=Lilita+One&family=Crimson+Text:ital,wght@0,400;0,600;1,400&family=Cinzel:wght@700;900&display=swap" rel="stylesheet">
<style>
:root{
  --gold:#e6ac1c;
  --gold-light:#f3cf4a;
  --gold-deep:#b9820c;
  --amber:#8a5f0a;
  --brown:#5b3a08;
  --brown-dark:#2a1804;
  --cream:#fff6d8;
  --ink:#3a3a3a;
  --white:#ffffff;
}
*{margin:0;padding:0;box-sizing:border-box}
html,body{width:928px;height:1200px;overflow:hidden}
body{position:relative;font-family:"Open Sans",sans-serif;
  background:radial-gradient(ellipse at 85% 10%,#f6d45a 0%,#e3ac1e 35%,#b77c0c 75%,#8a5807 100%)}
.abs{position:absolute}
.page{position:absolute;left:65px;top:0;width:797px;height:1122px;
  background:linear-gradient(180deg,#b8870f 30%,#8a5c0a 60%,#5a3806 100%);
  box-shadow:0 0 18px rgba(60,30,0,.5)}
.header{position:absolute;left:65px;top:0;width:797px;height:160px;background:#f7f7f5}
.hero{z-index:2}
.brand{left:78px;top:34px;display:flex;align-items:center;gap:12px;z-index:3}
.brand-mark{width:40px;height:40px;background:#1d1d1d;border:2px solid var(--gold)}
.brand-name{font-family:"Crimson Text",serif;font-weight:600;font-size:30px;color:var(--gold-deep);letter-spacing:1px}
.nav{left:447px;top:24px;display:flex;font-weight:300;font-size:15px;color:#8c7a55;z-index:3}
.nav a{color:inherit;text-decoration:none;height:27px;line-height:27px;padding:0 11px;margin-right:17px}
.nav a.active{background:#3d3d3d;color:#fff}
.call-label{right:87px;top:71px;font-size:11px;font-weight:600;color:#333;z-index:3}
.call-line{left:672px;top:89px;width:170px;height:1px;background:#ccc;z-index:3}
.call-number{right:73px;top:88px;font-weight:300;font-size:28px;color:#6a5a3a;z-index:3}
.hero-title{left:522px;top:148px;color:#fff;text-shadow:0 2px 4px rgba(0,0,0,.5);z-index:3}
.hero-title .small{font-family:"Cinzel",serif;font-weight:900;font-size:27px;color:#f0d48a;margin-left:42px;line-height:28px;display:block}
.hero-title .big{font-weight:700;font-size:38px;line-height:40px;display:block}
.arrow{width:41px;height:34px;background:#2a2a2a;display:flex;align-items:center;justify-content:center;z-index:3}
.arrow.left{left:54px;top:230px;border-radius:0 17px 17px 0}
.arrow.right{left:834px;top:241px;border-radius:17px 0 0 17px}
.panel{border:1px solid rgba(255,220,140,.35);background:linear-gradient(180deg,rgba(120,80,5,.25),rgba(80,50,5,.35));
  box-shadow:0 2px 6px rgba(0,0,0,.25)}
.heading{font-family:"Lilita One",sans-serif;color:var(--gold-light);text-shadow:0 1px 0 #fff6,0 2px 3px rgba(0,0,0,.4);line-height:1}
.sub{font-size:10px;font-weight:700;letter-spacing:2.2px;color:#fff}
.practice-list{left:86px;top:466px;width:186px;list-style:none}
.practice-list li{height:24px;border-bottom:1px dashed rgba(255,220,140,.35);display:flex;align-items:center;
  font-size:10.5px;font-weight:700;color:#fff;padding-left:27px;position:relative}
.practice-list li::before{content:"";position:absolute;left:5px;top:6px;width:12px;height:12px;border-radius:50%;
  background:radial-gradient(circle,#fff27a,#d9a300);box-shadow:0 0 0 1px #8a6400}
.practice-list li:last-child{border-bottom:none}
.team-photo{left:333px;top:468px;width:217px;height:111px;background:#fff;padding:5px}
.team-photo div{width:100%;height:100%;background:linear-gradient(180deg,#eef0f2,#9aa3ad 55%,#2e3640)}
.body-text{font-size:10px;line-height:14.5px;color:#f3e7c6;letter-spacing:.2px}
.side-box{left:607px;width:222px}
.cta-word{font-family:"Lilita One",sans-serif;font-size:38px;color:var(--gold-light);line-height:1}
.cta-sub{font-size:13.5px;font-weight:700;color:#fff;letter-spacing:1px}
.badge{left:639px;top:594px;width:158px;height:76px;background:#fbf6ea;border:1px solid #e4d9bf}
.video-thumb{left:618px;top:762px;width:44px;height:41px;background:#111;border:1px solid #888;display:flex;align-items:center;justify-content:center}
.input{left:610px;width:216px;border:1px solid rgba(255,220,140,.45);background:rgba(80,50,5,.2);
  font-size:10px;color:#f3e7c6;padding:4px 7px;letter-spacing:.3px}
.submit{left:764px;top:1074px;width:60px;height:19px;background:linear-gradient(#4a4a4a,#1a1a1a);border-radius:4px;
  color:#fff;font-size:10px;font-weight:700;text-align:center;line-height:19px}
.testimonial{left:76px;top:709px;width:496px;height:193px;background:#8f620a;border:1px solid #d6a42a}
.testimonial .inner{position:absolute;inset:7px;border:1px solid #d6a42a}
.quote{left:109px;top:777px;width:444px;font-family:"Crimson Text",serif;font-style:italic;font-size:15.6px;
  line-height:20.8px;color:#fff4d4;text-align:justify}
.articles p{position:relative;font-size:9.4px;line-height:13px;color:#f3e7c6;letter-spacing:.2px}
.articles p::before{content:"";position:absolute;left:-11px;top:4px;border-left:4px solid var(--gold);border-top:3px solid transparent;border-bottom:3px solid transparent}
.footer{left:0;top:1122px;width:928px;height:78px;background:linear-gradient(#2c1b05,#1a0f02)}
.footer-links{left:300px;top:1153px;width:310px;text-align:center;font-size:9.6px;color:var(--gold);letter-spacing:.3px;line-height:13px}
.footer-links span{margin:0 6px}
.footer-phone{left:704px;top:1144px;font-weight:300;font-size:27px;color:#8f7a55}
</style>
</head>
<body>
<div class="page"></div>
<div class="header"></div>

<!-- Practice -->
<div class="abs panel" style="left:72px;top:355px;width:208px;height:331px;border-top:none"></div>
<!-- Company -->
<div class="abs panel" style="left:306px;top:355px;width:269px;height:331px;border-top:none"></div>
<!-- Sidebar column -->
<div class="abs panel" style="left:600px;top:355px;width:237px;height:752px;border-top:none"></div>

<!-- hero imagery and gold swirl bands -->
<svg class="abs hero" style="left:65px;top:60px" width="797" height="372" viewBox="0 0 797 372">
  <defs>
    <linearGradient id="band" x1="0" x2="1"><stop offset="0" stop-color="#a47000"/><stop offset=".5" stop-color="#e9b526"/><stop offset="1" stop-color="#b98100"/></linearGradient>
  </defs>
  <foreignObject x="0" y="0" width="797" height="372">
    <div role="img" aria-label="Photo of a thoughtful woman resting her chin on her hands with a man seated out of focus behind her" style="width:797px;height:372px;background:linear-gradient(90deg,#d9cdb4 0%,#c7ab86 30%,#9aa0a2 55%,#8a9360 80%,#6d7a3e 100%);clip-path:path('M0 76 C120 104 200 32 320 22 C470 10 600 84 797 76 L797 345 C700 320 620 262 520 272 C400 286 300 342 200 334 C120 326 40 290 0 292 Z')"></div>
  </foreignObject>
  <path d="M0 68 C120 98 200 28 320 18 C470 6 600 78 797 68 L797 82 C600 92 470 28 320 40 C200 50 120 118 0 82 Z" fill="url(#band)"/>
  <path d="M0 290 C40 288 120 324 200 332 C300 340 400 284 520 270 C620 260 700 318 797 343 L797 362 C700 338 620 284 520 292 C400 304 300 362 200 354 C120 346 40 306 0 306 Z" fill="url(#band)"/>
</svg>

<div class="abs brand"><span class="brand-mark"></span><span class="brand-name">Ashcombe Law</span></div>
<nav class="abs nav"><a class="active" href="#">Home</a><a href="#">Meet Our Attorney</a><a href="#">FAQ</a><a href="#">Contact Us</a></nav>
<div class="abs call-label">Call Us Today</div>
<div class="abs call-line"></div>
<div class="abs call-number">123 456 7890</div>

<div class="abs hero-title"><span class="small">LEGEL</span><span class="big">SEPERATION</span></div>
<div class="abs arrow left"><svg width="12" height="14"><path d="M3 1 L10 7 L3 13" stroke="#fff" stroke-width="3" fill="none"/></svg></div>
<div class="abs arrow right"><svg width="12" height="14"><path d="M9 1 L2 7 L9 13" stroke="#fff" stroke-width="3" fill="none"/></svg></div>

<!-- Practice content -->
<div class="abs heading" style="left:88px;top:410px;font-size:31px">Practice</div>
<div class="abs sub" style="left:90px;top:441px">LOCATION OF AREAS</div>
<ul class="abs practice-list">
  <li>Divorce</li><li>Legal Separation</li><li>Paternity</li><li>Spousal Maintenance</li><li>Child Custody</li>
  <li>Child Support</li><li>Protective Orders</li><li>Community Property Business</li><li>Evaluations</li>
</ul>

<!-- Company content -->
<div class="abs heading" style="left:325px;top:405px;font-size:31px">Company</div>
<div class="abs sub" style="left:330px;top:441px">WELCOME MESSAGE</div>
<div class="abs team-photo"><div role="img" aria-label="Photo of a smiling business team seated in a row"></div></div>
<p class="abs body-text" style="left:322px;top:590px;width:236px;text-align:justify">Quisque rhoncus, turpis sed vehicula adipiscing, urna massa bibendum erat, vel rhoncus eros sapien sed tellus. Nam vehicula nisi sed sem vulputate nec posuere enim venenatis. Sed a arcu sed nisi porttitor lacinia vel eget magna. .</p>

<!-- Sidebar content -->
<div class="abs panel side-box" style="top:416px;height:110px;z-index:3"></div>
<svg class="abs" style="left:620px;top:432px;z-index:4" width="36" height="74"><rect x="1" y="1" width="34" height="72" rx="6" fill="#222" stroke="#aaa"/><rect x="4" y="10" width="28" height="50" fill="#7a8aa0"/><circle cx="18" cy="66" r="3" fill="#555"/></svg>
<div class="abs cta-word" style="left:660px;top:428px;z-index:4">CLICK</div>
<div class="abs cta-sub" style="left:666px;top:464px;z-index:4">CALL-US-NOW</div>
<p class="abs body-text" style="left:665px;top:480px;width:165px;font-size:9.8px;line-height:13px;z-index:4">Have a question about your case? Click here to connect to our office.</p>

<div class="abs panel side-box" style="top:546px;height:140px"></div>
<svg class="abs" style="left:616px;top:550px" width="34" height="36"><rect x="3" y="6" width="20" height="28" fill="#1e3350"/><path d="M18 8 h14 v6 a7 7 0 0 1 -14 0z" fill="#e7b22a"/><rect x="22" y="21" width="6" height="8" fill="#c99310"/></svg>
<div class="abs heading" style="left:657px;top:553px;font-size:24px">Awards</div>
<div class="abs badge" role="img" aria-label="Award badge placeholder"></div>

<div class="abs panel side-box" style="top:706px;height:118px"></div>
<svg class="abs" style="left:617px;top:714px" width="30" height="30"><rect x="2" y="6" width="26" height="20" fill="#555"/><rect x="2" y="2" width="26" height="5" fill="#999"/><rect x="14" y="12" width="10" height="10" fill="#ccc"/></svg>
<div class="abs heading" style="left:656px;top:716px;font-size:24px">Video Centre</div>
<div class="abs video-thumb"><svg width="14" height="16"><path d="M1 1 L13 8 L1 15Z" fill="#fff"/></svg></div>
<p class="abs body-text" style="left:672px;top:762px;width:152px;font-size:9.8px">Need more information? Learn more about your case from our informative videos</p>

<svg class="abs" style="left:608px;top:848px" width="40" height="42"><circle cx="15" cy="11" r="8" fill="#f2f2f2"/><path d="M3 34 a12 12 0 0 1 24 0z" fill="#f2f2f2"/><path d="M20 38 L36 20 L38 24 L24 40Z" fill="#e08a10"/></svg>
<div class="abs heading" style="left:656px;top:857px;font-size:24px">Quick Email</div>
<div class="abs" style="left:608px;top:895px;width:217px;border-top:1px dashed rgba(255,220,140,.5)"></div>
<p class="abs body-text" style="left:611px;top:903px;width:214px;text-align:justify;font-size:9.8px">Send us a quick email with any questions or concerns you may have about your potential case.</p>
<div class="abs input" style="top:956px;height:21px">Your Name</div>
<div class="abs input" style="top:983px;height:21px">Your Email Address</div>
<div class="abs input" style="top:1012px;height:54px">Tell Us About Your Case.</div>
<div class="abs submit">Submit</div>

<!-- Testimonial -->
<div class="abs testimonial"><div class="inner"></div></div>
<svg class="abs" style="left:92px;top:724px" width="40" height="36"><rect x="2" y="2" width="24" height="18" rx="4" fill="#f08a1a"/><rect x="11" y="9" width="26" height="18" rx="4" fill="#ffd23c"/><path d="M18 27 l-4 7 l10-7z" fill="#ffd23c"/></svg>
<div class="abs heading" style="left:145px;top:724px;font-size:30px">Recent Testimonial</div>
<div class="abs" style="left:92px;top:766px;width:465px;border-top:2px dotted rgba(255,230,160,.55)"></div>
<p class="abs quote"><span style="position:absolute;left:-20px;top:-4px;font-size:26px;font-style:normal">“</span>Praesent et turpis dui. Phasellus porta est vel tortor interdum nec laoreet turpis gravida. Cras accumsan imperdiet auctor. Ut dictum, nisl mattis tempor auctor, leo risus bibendum diam, at vehicula orci velit id enim. Nunc eget augue purus, et tincidunt velit. Ut ultrices nisl sit amet leo auctor eu suscipit magna vestibulum. &nbsp;- Daniel Reyes <span style="font-style:normal;font-size:20px">”</span></p>

<!-- Articles -->
<svg class="abs" style="left:92px;top:927px" width="42" height="42"><rect x="2" y="4" width="26" height="30" fill="#f4f4f4" stroke="#bbb"/><circle cx="18" cy="20" r="8" fill="none" stroke="#666" stroke-width="2"/><path d="M24 26 L36 38" stroke="#333" stroke-width="4"/></svg>
<div class="abs heading" style="left:145px;top:929px;font-size:30px">Latest Articles</div>
<div class="abs" style="left:91px;top:973px;width:485px;height:1px;background:#c99a2e"></div>
<div class="abs articles" style="left:117px;top:995px;width:452px">
  <p>Aenean ac diam eu erat suscipit dapibus in ac neque. Curabitur non nisi ut lorem accumsan cursus nec in odio. Praesent hendrerit, lacus at eleifend commodo, massa sapien accumsan diam, et sollici tudin diam mauris at arcu.</p>
  <p style="margin-top:17px">Aenean ac diam eu erat suscipit dapibus in ac neque. Curabitur non nisi ut lorem accumsan cursus nec in odio. Praesent hendrerit, lacus at eleifend commodo, massa sapien accumsan diam, et sollici tudin diam mauris at arcu.</p>
</div>
<div class="abs" style="left:510px;top:1091px;font-size:9px;font-weight:700;color:#fff">View All [+]</div>

<!-- Footer -->
<div class="abs footer"></div>
<div class="abs" style="left:88px;top:1150px;width:32px;height:32px;background:#1d1d1d;border:2px solid var(--gold)"></div>
<div class="abs footer-links">Home<span>~</span>Meet Our Attorney<span>~</span>FAQ<span>~</span>Contact Us<br>© 2012 All Rights Reserved.</div>
<svg class="abs" style="left:671px;top:1150px" width="28" height="28"><circle cx="14" cy="14" r="12.5" fill="none" stroke="#8f7a55" stroke-width="2"/><path d="M9 8 c1-1 3-1 3 1 l0 2 c0 1-1 1-1 2 c1 2 2 3 4 4 c1 0 1-1 2-1 l2 0 c2 0 2 2 1 3 c-2 2-5 1-8-2 c-3-3-4-6-3-9z" fill="#8f7a55"/></svg>
<div class="abs footer-phone">123 456 7890</div>
</body>
</html>
```